Business Cards

Need business card design that I can update for new employees and details. Needs to incorporate our logo, be bright and fun (in line with tourism and holidays)
Would like a Map of Western Australia on the front with locations all the caravan parks we own (just purchased Tom Price so please include that as well as others listed on our website).
Target Market(s)
Famillies
Contact Information for Business Card
5 Cards -
Neil Perrow (Director) e: perrow@wattlebay.com.au p: 0491 570 156
Mira Perrow (Director) e: perrow@wattlebay.com.au p: 0491 570 157
Owen Halvey (General Manager) e: halvey@wattlebay.com.au p: 0491 570 158
Helen Halvey (General Manager) e: halvey@wattlebay.com.au p: 0491 570 159
Colin Danby (Training and Operations Manager) - e: danby@wattlebay.com.au p:0491 570 110
Colors
Look and feel

```html
<!DOCTYPE html>
<html lang="en">
<head>
<meta charset="utf-8">
<title>Wattlebay Tourist Parks – Business Card</title>
<link rel="stylesheet" href="https://fonts.googleapis.com/css2?family=Roboto:wght@400;500&family=Roboto+Condensed:wght@700&display=swap">
<style>
  :root {
    --backdrop: #2b2b2b;
    --paper: #f3f3f3;
    --sea-green: #66b6a8;
    --lagoon: #3fb8c2;
    --ink: #4a4a4a;
    --white: #ffffff;
  }
  html, body {
    margin: 0;
    width: 1200px;
    height: 960px;
    overflow: hidden;
    background: var(--backdrop);
    font-family: "Roboto", Arial, sans-serif;
  }
  .card {
    position: absolute;
    width: 600px;
    height: 343px;
    overflow: hidden;
  }
  .card--front { left: 314px; top: 113px; background: var(--paper); }
  .card--back  { left: 311px; top: 472px; background: var(--lagoon); }

  .card__wave { position: absolute; inset: 0; }

  .brand {
    position: absolute;
    display: flex;
    flex-direction: column;
    align-items: center;
    font-family: "Roboto", Arial, sans-serif;
    font-weight: 400;
    text-transform: uppercase;
  }
  .brand__square {
    width: 66px;
    height: 66px;
    border: 3px solid currentColor;
    box-sizing: border-box;
    margin-bottom: 12px;
  }
  .brand__name {
    margin: 0;
    font-size: 27px;
    letter-spacing: 3px;
    line-height: 1;
    text-align: center;
  }
  .brand__name span { display: block; font-size: 13px; letter-spacing: 3px; margin-top: 8px; }

  .card--front .brand { left: 340px; top: 44px; width: 225px; color: var(--ink); }
  .card--front .brand__square { border-color: var(--lagoon); background: var(--sea-green); }

  .card--back .brand { left: 150px; top: 100px; width: 300px; color: var(--white); }
  .card--back .brand__square { width: 92px; height: 92px; margin-bottom: 16px; }
  .card--back .brand__name { font-size: 34px; letter-spacing: 4px; }
  .card--back .brand__name span { font-size: 15px; letter-spacing: 4px; margin-top: 10px; }

  .person {
    position: absolute;
    left: 39px;
    top: 193px;
    color: var(--white);
  }
  .person__name {
    margin: 0;
    font-family: "Roboto Condensed", "Arial Narrow", sans-serif;
    font-weight: 700;
    font-size: 21px;
    text-transform: uppercase;
  }
  .person__role {
    margin: 3px 0 14px;
    font-size: 15px;
    font-weight: 500;
    text-transform: uppercase;
  }
  .contact { list-style: none; margin: 0; padding: 0; font-size: 14px; }
  .contact li { display: flex; align-items: center; height: 19px; }
  .contact svg { width: 13px; height: 13px; margin-right: 6px; fill: var(--white); }

  .card__url {
    position: absolute;
    left: 0; right: 0;
    top: 294px;
    margin: 0;
    text-align: center;
    color: var(--white);
    font-size: 14px;
    letter-spacing: 2.5px;
  }
</style>
</head>
<body>

<section class="card card--front" aria-label="Card front">
  <svg class="card__wave" viewBox="0 0 600 343" aria-hidden="true">
    <path d="M0,138 C140,118 240,126 330,196 C420,266 490,298 600,278 L600,343 L0,343 Z" fill="var(--lagoon)"/>
    <path d="M0,150 C140,130 240,138 330,208 C420,278 490,306 600,288 L600,343 L0,343 Z" fill="var(--sea-green)"/>
    <path d="M0,146 C140,126 240,134 330,204 C420,274 490,303 600,284" fill="none" stroke="var(--white)" stroke-width="2"/>
  </svg>

  <div class="brand">
    <div class="brand__square"></div>
    <p class="brand__name">Wattlebay<span>Tourist Parks</span></p>
  </div>

  <div class="person">
    <h1 class="person__name">Neil Perrow</h1>
    <p class="person__role">Director</p>
    <ul class="contact">
      <li><svg viewBox="0 0 24 24"><path d="M6.6 10.8a15 15 0 0 0 6.6 6.6l2.2-2.2a1 1 0 0 1 1-.25 11.4 11.4 0 0 0 3.6.57 1 1 0 0 1 1 1V20a1 1 0 0 1-1 1A17 17 0 0 1 3 4a1 1 0 0 1 1-1h3.5a1 1 0 0 1 1 1c0 1.25.2 2.45.57 3.57a1 1 0 0 1-.25 1z"/></svg>0491 570 156</li>
      <li><svg viewBox="0 0 24 24"><path d="M2 5h20v14H2z" opacity="0"/><path d="M2 5h20v2l-10 6L2 7zM2 9l10 6 10-6v10H2z"/></svg>perrow@wattlebay.com.au</li>
      <li><svg viewBox="0 0 24 24"><path d="M12 2a10 10 0 1 0 0 20 10 10 0 0 0 0-20zm-1 17.9A8 8 0 0 1 4.2 10L9 14.8v1a2 2 0 0 0 2 2zm6.9-2.5a2 2 0 0 0-1.9-1.4h-1v-3a1 1 0 0 0-1-1H8v-2h2a1 1 0 0 0 1-1V7h2a2 2 0 0 0 2-2v-.4a8 8 0 0 1 2.9 12.8z"/></svg>www.wattlebay.com.au</li>
    </ul>
  </div>
</section>

<section class="card card--back" aria-label="Card back">
  <div class="brand">
    <div class="brand__square"></div>
    <p class="brand__name">Wattlebay<span>Tourist Parks</span></p>
  </div>
  <p class="card__url">www.wattlebay.com.au</p>
</section>

</body>
</html>
```